Brook Refrigeration. Refrigeration and air conditioning specialists.

We need a website to promote our business. We would a modern simple design using the colours from our logo and black. We want it to be fun but proffesional.

Target Market(s)

Commercial

Number of Pages Required

4 page

Requirements
Must have
• Home Page, About Us, Services and Contact Us.
• 24/7 365 days service available.
• Brook Refrigeration's dedicated team specialises in commercial refrigeration and air conditioning equipment.
• Based in Joondalup, we cover Perth Metro and surrounding areas.
Nice to have
• KNOWLEDGE . EXPERIENCE . PASSION in bold.
• Our experienced and highly trained technicians provide extensive knowledge and exceptional skills for your commercial refrigeration and air conditioning requirements.
• Pictures of commercial refrigeration.
Should not have
• No mention of domestic services.

```html
<!DOCTYPE html>
<html lang="en">
<head>
<meta charset="utf-8">
<title>Brook Refrigeration</title>
<link rel="stylesheet" href="https://fonts.googleapis.com/css2?family=Jost:wght@300;400&family=Roboto:wght@300;400;500;700;900&family=Roboto+Condensed:wght@400;700&display=swap">
<style>
:root{
  --lime:#a6ee6c;
  --lime-dark:#8fd955;
  --purple:#3d2660;
  --purple-deep:#2f1c4d;
  --ink:#2b2b2b;
  --text:#555;
  --footer:#323232;
  --white:#fff;
  --line:#bdbdbd;
}
*{box-sizing:border-box;margin:0;padding:0}
html,body{width:1200px;height:3711px;overflow:hidden}
body{position:relative;background:var(--white);font-family:"Roboto",sans-serif;color:var(--text)}
.abs{position:absolute}

/* header */
.site-header{position:absolute;left:0;top:0;width:1200px;height:135px;border-top:5px solid var(--lime);background:var(--white)}
.brand{position:absolute;left:82px;top:28px;display:flex;flex-direction:column;align-items:center}
.brand-name{font-family:"Roboto",sans-serif;font-weight:900;font-size:46px;color:var(--lime);line-height:1;letter-spacing:1px}
.brand-sub{font-family:"Roboto",sans-serif;font-weight:900;font-size:13px;color:var(--lime);letter-spacing:1px;margin-top:4px}
.top-phone{position:absolute;left:636px;top:34px;font-size:20px;font-weight:500;color:var(--ink);display:flex;align-items:center;gap:10px}
.social{position:absolute;left:864px;top:36px;display:flex;gap:4px}
.social span{width:21px;height:21px;display:block;background:#3f6fb3}
.social span:nth-child(2){background:#d24a3a}
.social span:nth-child(3){background:#3fa9e0}
.social span:nth-child(4){background:#2a78b6}
.badge{position:absolute;left:1040px;top:14px;width:120px;text-align:center;color:var(--purple)}
.badge-dot{width:32px;height:32px;border-radius:50%;border:3px solid var(--purple);margin:0 auto 2px}
.badge-text{font-family:"Roboto Condensed",sans-serif;font-weight:700;font-size:22px;line-height:1}
.badge-text small{font-size:11px;vertical-align:middle}
.badge-note{font-size:7px;letter-spacing:.5px}
.main-nav{position:absolute;left:395px;top:92px;width:805px;height:43px}
.main-nav svg{position:absolute;left:0;top:0}
.nav-list{position:absolute;left:56px;top:9px;display:flex;list-style:none;font-size:15px;color:var(--white);letter-spacing:.5px}
.nav-list li{padding:4px 22px;border-right:1px solid rgba(255,255,255,.6);line-height:17px}
.nav-list li:last-child{border-right:none}
.nav-list li.active{background:var(--lime);color:var(--purple);padding:4px 12px;margin-right:14px;border-right:none}
.search{position:absolute;left:535px;top:10px;width:180px;height:24px;background:var(--white);font-size:11px;color:#555;padding:5px 8px}
.search svg{position:absolute;right:6px;top:6px}

/* hero */
.hero{position:absolute;left:0;top:135px;width:1200px;height:705px;background:linear-gradient(180deg,#5a6470 0%,#3c4148 45%,#2a2d31 100%);text-align:center;color:var(--white)}
.hero-kicker{position:absolute;left:0;right:0;top:196px;font-family:"Jost",sans-serif;font-weight:300;font-size:44px}
.hero-title{position:absolute;left:0;right:0;top:250px;font-family:"Roboto Condensed",sans-serif;font-weight:700;font-size:57px;line-height:73px}
.hero-values{position:absolute;left:0;right:0;top:400px;font-family:"Roboto Condensed",sans-serif;font-weight:700;font-size:47px;color:var(--lime)}
.btn-lime{background:var(--lime);color:var(--purple);font-family:"Roboto Condensed",sans-serif;text-align:center}
.hero-cta{position:absolute;left:515px;top:485px;width:192px;height:46px;line-height:46px;font-size:22px;border-radius:4px}
.dots{position:absolute;left:580px;top:646px;display:flex;gap:10px}
.dots i{width:9px;height:9px;border-radius:50%;border:1.5px solid var(--white);display:block}
.dots i:first-child{background:var(--white)}

/* about */
.about{position:absolute;left:0;top:840px;width:1200px;height:648px}
.section-title{font-family:"Jost",sans-serif;font-weight:400;color:var(--purple)}
.about h2{position:absolute;left:131px;top:88px;font-size:30px}
.about-copy{position:absolute;left:131px;top:160px;width:450px;font-size:12.5px;line-height:19.5px;color:#555}
.about-copy p{margin-bottom:19px}
.about-photo{position:absolute;left:705px;top:65px;width:350px;height:583px;background:linear-gradient(180deg,#eef0f3 0%,#c9d1dc 40%,#2f3f6a 70%,#24305a 100%);border-radius:170px 170px 0 0}

/* services */
.services{position:absolute;left:0;top:1488px;width:1200px;height:1057px;background:var(--purple)}
.services h2{position:absolute;left:0;right:0;top:56px;text-align:center;font-family:"Jost",sans-serif;font-weight:400;font-size:28px;color:var(--lime)}
.rule{position:absolute;height:2px;background:var(--lime)}
.services-intro{position:absolute;left:130px;width:940px;top:136px;text-align:center;font-size:12.5px;line-height:24px;color:#e6e0ef}
.card{position:absolute;width:292px;height:245px;background:var(--white);text-align:center}
.card-icon{position:absolute;left:91px;top:-50px;width:110px;height:110px;border-radius:50%;background:var(--white);border:3px solid var(--purple);padding:10px}
.card-icon div{width:100%;height:100%;border-radius:50%;background:radial-gradient(circle,#e9ecef 0%,#c3c8cf 70%,#fff 100%)}
.card h3{position:absolute;left:0;right:0;top:88px;font-size:18px;font-weight:500;color:var(--purple)}
.card .card-rule{position:absolute;left:126px;top:116px;width:40px;height:1px;background:var(--purple)}
.card p{position:absolute;left:28px;right:28px;top:126px;font-size:12px;line-height:16px;color:#666}
.card .more{position:absolute;left:0;right:0;top:208px;font-size:12px;color:var(--purple);text-decoration:underline}
.services-cta{position:absolute;left:525px;top:955px;width:150px;height:36px;line-height:36px;font-size:12px;font-weight:700}

/* contact */
.contact{position:absolute;left:0;top:2545px;width:1200px;height:615px}
.contact h2{position:absolute;left:0;right:0;top:82px;text-align:center;font-family:"Roboto",sans-serif;font-weight:500;font-size:32px;color:var(--purple)}
.field-label{position:absolute;font-size:14px;color:var(--text)}
.field-label b{color:var(--purple);font-weight:400}
.input{position:absolute;border:1px solid #aaa;background:var(--white)}
.check{position:absolute;left:675px;top:398px;font-size:14px;display:flex;align-items:center;gap:12px}
.check i{width:16px;height:16px;border:1px solid #aaa;display:block}
.submit{position:absolute;left:533px;top:485px;width:134px;height:37px;line-height:37px;background:var(--purple);color:var(--white);text-align:center;font-size:16px;font-weight:500;border-radius:3px}

/* newsletter */
.newsletter{position:absolute;left:0;top:3160px;width:1200px;height:153px;background:var(--lime)}
.newsletter h2{position:absolute;left:172px;top:63px;font-family:"Roboto Condensed",sans-serif;font-weight:700;font-size:24px;color:var(--purple)}
.newsletter .input{left:382px;top:55px;width:506px;height:48px;border:none}
.newsletter .btn{position:absolute;left:888px;top:55px;width:127px;height:48px;line-height:48px;background:var(--purple);color:var(--white);text-align:center;font-size:14px;font-weight:500}

/* footer */
.site-footer{position:absolute;left:0;top:3313px;width:1200px;height:323px;background:var(--footer);color:var(--white)}
.footer-brand{position:absolute;left:110px;top:72px;display:flex;flex-direction:column;align-items:center}
.footer-brand .brand-name{color:var(--white);font-size:52px}
.footer-brand .brand-sub{color:var(--white);font-size:14px}
.footer-title{position:absolute;top:62px;font-family:"Roboto Condensed",sans-serif;font-weight:700;font-size:18px;color:var(--lime)}
.footer-item{position:absolute;left:358px;display:flex;gap:12px}
.footer-item h4{font-family:"Roboto Condensed",sans-serif;font-weight:700;font-size:15px;color:var(--lime);margin-bottom:4px}
.footer-item p{font-size:14px;line-height:19px}
.footer-links{position:absolute;left:630px;top:112px;list-style:none;font-size:15px;line-height:34px}
.f-input{position:absolute;height:38px;background:var(--white);border:2px solid #ddd;font-size:13px;color:#777;padding:9px 10px}
.f-send{position:absolute;left:794px;top:202px;width:130px;height:38px;line-height:38px;font-size:16px;font-weight:700}
.copyright{position:absolute;left:0;top:3636px;width:1200px;height:75px;background:var(--purple);color:#d9d2e6;text-align:center;font-size:12px;line-height:75px}
</style>
</head>
<body>

<header class="site-header">
  <div class="brand">
    <span class="brand-name">BROOK</span>
    <span class="brand-sub">REFRIGERATION</span>
  </div>
  <div class="top-phone">
    <svg width="14" height="22" viewBox="0 0 14 22"><rect x="1" y="1" width="12" height="20" rx="2" fill="none" stroke="#3d2660" stroke-width="2"/><rect x="5" y="17" width="4" height="1.5" fill="#3d2660"/></svg>
    1-800-555-0147
  </div>
  <div class="social"><span></span><span></span><span></span><span></span></div>
  <div class="badge">
    <div class="badge-dot"></div>
    <div class="badge-text">24/7 <small>365 DAYS</small></div>
    <div class="badge-note">SERVICE AVAILABLE</div>
  </div>
  <nav class="main-nav">
    <svg width="805" height="43" viewBox="0 0 805 43"><path d="M0 43 C28 43 30 0 60 0 H805 V43 Z" fill="#3d2660"/></svg>
    <ul class="nav-list">
      <li class="active">HOME</li>
      <li>ABOUT US</li>
      <li>SERVICES</li>
      <li>CONTACT US</li>
    </ul>
    <div class="search">Search
      <svg width="11" height="11" viewBox="0 0 11 11"><circle cx="4.5" cy="4.5" r="3.5" fill="none" stroke="#555" stroke-width="1.5"/><line x1="7" y1="7" x2="10.5" y2="10.5" stroke="#555" stroke-width="1.5"/></svg>
    </div>
  </nav>
</header>

<section class="hero" role="img" aria-label="Rows of commercial air conditioning condenser units on a rooftop under a cloudy sky">
  <p class="hero-kicker">Our dedicated team specialises in</p>
  <h1 class="hero-title">COMMERCIAL REFRIGERATION &amp;<br>AIR CONDITIONING EQUIPMENT.</h1>
  <p class="hero-values">KNOWLEDGE • EXPERIENCE • PASSION</p>
  <div class="hero-cta btn-lime">KNOW MORE</div>
  <div class="dots"><i></i><i></i><i></i></div>
</section>

<section class="about">
  <h2 class="section-title">About us</h2>
  <div class="about-copy">
    <p>Brook Refrigeration's dedicated team specialises in commercial refrigeration and air conditioning equipment. Based in Joondalup, we cover Perth Metro and surrounding areas.</p>
    <p>Our experienced and highly trained technicians provide extensive knowledge and exceptional skills for your commercial refrigeration and air conditioning requirements. From a single display fridge to a full cool room fit-out, we design, install and maintain systems that keep your stock safe, your energy bills low and your customers comfortable all year round.</p>
    <p>Breakdowns never wait for business hours, so neither do we. Our service vans are stocked with common parts and our team is on call 24 hours a day, 365 days a year, ready to get your cafe, restaurant, supermarket or warehouse back up and running fast.</p>
  </div>
  <div class="about-photo" role="img" aria-label="Smiling technician in a cap and navy work shirt holding a clipboard"></div>
</section>

<section class="services">
  <h2>Our Services</h2>
  <div class="rule" style="left:572px;top:104px;width:56px"></div>
  <p class="services-intro">Whether you wish to cool, store or display food and drink, we have a wide range of commercial refrigerator services catering to various small and large scale industries.<br>We specialize in wide range of commercial refrigeration operations and maintenance services to ensure efficient functioning of the systems.</p>

  <article class="card" style="left:131px;top:283px">
    <div class="card-icon"><div role="img" aria-label="Commercial chest freezer"></div></div>
    <h3>Commercial Freezer</h3><span class="card-rule"></span>
    <p>Chest and upright freezers that hold a steady temperature, installed and serviced by our trained technicians.</p>
    <span class="more">read more»</span>
  </article>
  <article class="card" style="left:455px;top:283px">
    <div class="card-icon"><div role="img" aria-label="Walk in cool room"></div></div>
    <h3>Walk In Cooler</h3><span class="card-rule"></span>
    <p>Custom cool rooms built to fit your space, with efficient panels, doors and reliable refrigeration units.</p>
    <span class="more">read more»</span>
  </article>
  <article class="card" style="left:779px;top:283px">
    <div class="card-icon"><div role="img" aria-label="Stainless steel kitchen refrigerator"></div></div>
    <h3>Kitchen Refrigeration</h3><span class="card-rule"></span>
    <p>Under-bench fridges, prep stations and upright cabinets that keep busy commercial kitchens running smoothly every day.</p>
    <span class="more">read more»</span>
  </article>
  <article class="card" style="left:131px;top:640px">
    <div class="card-icon"><div role="img" aria-label="Glass door drinks merchandiser"></div></div>
    <h3>Glass Door Merchandiser</h3><span class="card-rule"></span>
    <p>Bright, energy efficient display fridges that show off your drinks and keep every shelf perfectly chilled.</p>
    <span class="more">read more»</span>
  </article>
  <article class="card" style="left:455px;top:640px">
    <div class="card-icon"><div role="img" aria-label="Curved glass bakery display case"></div></div>
    <h3>Bakery Display Case</h3><span class="card-rule"></span>
    <p>Curved and square display cases that keep cakes, pastries and slices fresh while tempting your customers.</p>
    <span class="more">read more»</span>
  </article>
  <article class="card" style="left:779px;top:640px">
    <div class="card-icon"><div role="img" aria-label="Commercial ice machine"></div></div>
    <h3>Ice machines</h3><span class="card-rule"></span>
    <p>Ice makers and flakers for bars, cafes and seafood counters, supplied, installed and serviced on site.</p>
    <span class="more">read more»</span>
  </article>

  <div class="services-cta btn-lime">MORE SERVICE</div>
</section>

<section class="contact">
  <h2>Contact Us</h2>
  <div class="rule" style="left:562px;top:134px;width:76px;height:1px;background:#999"></div>
  <span class="field-label" style="left:155px;top:190px">Name <b>*</b></span>
  <div class="input" style="left:155px;top:213px;width:393px;height:38px"></div>
  <span class="field-label" style="left:155px;top:275px">Email <b>*</b></span>
  <div class="input" style="left:155px;top:298px;width:393px;height:38px"></div>
  <span class="field-label" style="left:155px;top:360px">Phone</span>
  <div class="input" style="left:155px;top:383px;width:393px;height:38px"></div>
  <span class="field-label" style="left:675px;top:190px">Description</span>
  <div class="input" style="left:675px;top:213px;width:395px;height:132px"></div>
  <span class="field-label" style="left:675px;top:360px;font-size:13px"><b>*</b> Required</span>
  <div class="check"><i></i>I have read the Disclaimer and Privacy Policy</div>
  <div class="submit">SUBMIT</div>
</section>

<section class="newsletter">
  <h2>NEWSLETTER</h2>
  <div class="input"></div>
  <div class="btn">SUBSCRIBE</div>
</section>

<footer class="site-footer">
  <div class="footer-brand">
    <span class="brand-name">BROOK</span>
    <span class="brand-sub">REFRIGERATION</span>
  </div>

  <h3 class="footer-title" style="left:358px">CONTACT US</h3>
  <div class="footer-item" style="top:107px">
    <svg width="22" height="28" viewBox="0 0 22 28"><path d="M11 1C5.5 1 1 5.3 1 10.8 1 18 11 27 11 27s10-9 10-16.2C21 5.3 16.5 1 11 1z" fill="#a6ee6c"/><circle cx="11" cy="10.5" r="4" fill="#323232"/></svg>
    <div><h4>ADDRESS</h4><p>42 Lakeside Drive<br>Joondalup WA 6027</p></div>
  </div>
  <div class="footer-item" style="top:188px">
    <svg width="22" height="22" viewBox="0 0 24 24"><path d="M6.6 10.8a15.1 15.1 0 0 0 6.6 6.6l2.2-2.2c.3-.3.7-.4 1-.2 1.1.4 2.3.6 3.6.6.6 0 1 .4 1 1V20c0 .6-.4 1-1 1A17 17 0 0 1 3 4c0-.6.4-1 1-1h3.5c.6 0 1 .4 1 1 0 1.3.2 2.5.6 3.6.1.3 0 .7-.2 1z" fill="#a6ee6c"/></svg>
    <div><h4>PHONE NUMBER</h4><p style="font-weight:700">1-800-555-0147</p></div>
  </div>

  <h3 class="footer-title" style="left:625px">ABOUT</h3>
  <ul class="footer-links"><li>Home</li><li>About Us</li><li>Services</li><li>Contact us</li></ul>

  <h3 class="footer-title" style="left:790px">GET IN TOUCH</h3>
  <div class="f-input" style="left:794px;top:104px;width:152px">Name</div>
  <div class="f-input" style="left:950px;top:104px;width:154px">Phone</div>
  <div class="f-input" style="left:794px;top:147px;width:310px">Email address</div>
  <div class="f-send btn-lime">SEND</div>
</footer>

<div class="copyright">© 2018 brookrefrigeration All Right Reserved</div>

</body>
</html>
```